Need a website setup for our new removalist business.
Our business is called Harbour Lane Removals and would like a website setup.
We don’t have a website, logo or design as of yet. Our truck is blue so something possibly that works and can incorporate the blue.

```html
<!DOCTYPE html>
<html lang="en">
<head>
<meta charset="utf-8">
<title>Harbour Lane Removals</title>
<link rel="stylesheet" href="https://fonts.googleapis.com/css2?family=Poppins:wght@400;500;600;700&display=swap">
<style>
:root{
  --navy:#1c2b4d;
  --navy-deep:#17233f;
  --blue:#1f6db3;
  --blue-bright:#2a7fc4;
  --ink:#2c2a20;
  --text:#3d3d3d;
  --sky:#d9e9f7;
  --pale:#eef5fc;
  --white:#ffffff;
  --gold:#8a7a4a;
}
*{box-sizing:border-box;margin:0;padding:0}
html,body{width:1200px;height:3093px;overflow:hidden}
body{position:relative;font-family:"Poppins",sans-serif;color:var(--text);background:var(--white)}
.abs{position:absolute}
.mark{background:linear-gradient(to top,var(--blue) 0,var(--blue) 12px,transparent 12px);padding:0 2px}

/* header */
.brand{left:112px;top:26px;font-weight:600;font-size:28px;line-height:33px;color:var(--navy)}
.brand span{display:block;color:var(--blue)}
.contact-item{top:20px;display:flex;align-items:center;gap:12px}
.contact-item .ico{width:44px;height:44px;border-radius:50%;background:var(--blue);display:flex;align-items:center;justify-content:center}
.contact-item p{font-size:15px;line-height:22px;color:#444}
.contact-item b{display:block;font-weight:500;color:var(--gold)}
.navbar{left:538px;top:85px;width:662px;height:51px;background:var(--navy);clip-path:polygon(0 0,100% 0,100% 100%,28px 100%)}
.navbar ul{list-style:none;display:flex;gap:33px;padding:21px 0 0 33px;font-size:16px;color:var(--white)}
.navbar li.active{font-weight:600}

/* hero */
.hero{left:0;top:114px;width:1200px;height:429px;background:var(--sky)}
.hero-photo{left:470px;top:114px;width:730px;height:429px;background:linear-gradient(90deg,var(--sky) 0%,#9fb3c0 25%,#7a6e5c 55%,#c09a6a 75%,#5d6b5a 100%)}
.hero h1{left:112px;top:216px;font-weight:600;font-size:64px;line-height:56px;color:var(--navy)}
.hero h1 small{display:block;font-size:37px;line-height:44px;color:var(--blue)}
.btn{display:inline-flex;align-items:center;justify-content:center;border-radius:30px;background:linear-gradient(90deg,var(--blue),var(--navy));color:var(--white);font-weight:600;font-size:16px}
.hero .btn{left:112px;top:404px;width:150px;height:48px}

/* services */
.section-title{width:1200px;left:0;text-align:center;font-weight:600;font-size:44px;color:var(--ink)}
.card{overflow:hidden}
.card .photo{position:absolute;inset:0}
.pill{position:absolute;right:0;height:54px;padding:0 22px 0 28px;background:var(--white);border-radius:27px 0 0 27px;display:flex;align-items:center;font-weight:500;font-size:19px;color:var(--ink)}
.card .overlay{position:absolute;left:0;right:0;bottom:0;height:135px;background:rgba(31,109,179,.88);color:var(--white);font-size:16px;line-height:28px;padding:10px 16px}

/* about */
.about-bg{left:0;top:1406px;width:1200px;height:566px;background:linear-gradient(90deg,#b79a70 0%,#d8c6a6 25%,#7e7e86 45%,#a89b8a 70%,#b7aa98 100%)}
.about-card{left:580px;top:1469px;width:510px;height:457px;background:var(--white);border-radius:0 6px 0 120px;padding:30px 50px 0 64px}
.about-card h2{font-weight:600;font-size:44px;color:var(--ink);margin-bottom:22px}
.about-card p{font-size:16px;line-height:28px;color:var(--text);margin-bottom:12px}
.about-card .btn{width:152px;height:44px;margin-top:12px}

/* testimonials */
.reviews{left:0;top:1972px;width:1200px;height:711px;background:var(--pale)}
.review{width:432px;height:249px;background:var(--white);padding:64px 24px 0 25px;box-shadow:0 2px 10px rgba(0,0,0,.05)}
.review h3{font-weight:400;font-size:18px;color:var(--ink);margin-bottom:10px}
.review p{font-size:16px;line-height:28px;color:var(--text)}
.review .badge{display:block;width:60px;height:26px;margin-top:8px;background:#e9eef5;border-radius:4px}
.quote{width:80px;height:80px;border-radius:50%;background:var(--navy);display:flex;align-items:center;justify-content:center}

/* newsletter */
.footer{left:0;top:2683px;width:1200px;height:410px;background:var(--navy-deep)}
.news{left:112px;top:2489px;width:977px;height:292px;border-radius:34px;background:var(--blue);text-align:center;color:var(--white)}
.news h2{font-weight:600;font-size:44px;margin-top:34px}
.news h2 .mark{background:linear-gradient(to top,#5b9bd3 0,#5b9bd3 10px,transparent 10px)}
.news p{font-size:18px;line-height:28px;margin:14px auto 0;width:680px}
.signup{position:absolute;left:219px;top:191px;width:538px;height:61px;background:var(--white);border-radius:31px;display:flex;align-items:center;justify-content:space-between;padding:0 4px 0 33px}
.signup span{color:#444;font-size:17px}
.signup b{width:127px;height:51px;border-radius:26px;background:var(--navy);display:flex;align-items:center;justify-content:center;font-weight:600;font-size:18px}

/* footer */
.footer-brand{left:112px;top:2866px;font-weight:600;font-size:29px;line-height:33px;color:var(--white)}
.socials{left:112px;top:2946px;display:flex;gap:7px}
.socials i{width:32px;height:32px;border:2px solid var(--white);border-radius:50%}
.copy{left:116px;top:2996px;font-size:16px;line-height:30px;color:var(--white)}
.col h4{font-weight:600;font-size:16px;letter-spacing:.5px;color:var(--white);margin-bottom:16px}
.col a{display:block;font-size:15px;line-height:28.5px;color:var(--white);text-decoration:none}
.col .row{display:flex;gap:20px;font-size:16px;line-height:26px;color:var(--white);margin-bottom:12px}
.col .row svg{flex:none;margin-top:4px}
</style>
</head>
<body>

<header>
  <div class="abs brand">Harbour Lane<span>Removals</span></div>
  <div class="abs contact-item" style="left:660px">
    <div class="ico"><svg width="22" height="22" viewBox="0 0 24 24" fill="none" stroke="#fff" stroke-width="2"><path d="M4 14v-2a8 8 0 0 1 16 0v2"/><rect x="3" y="13" width="4" height="6" rx="1"/><rect x="17" y="13" width="4" height="6" rx="1"/></svg></div>
    <p>Sales &amp; Service:<b>+1800-555-0142</b></p>
  </div>
  <div class="abs contact-item" style="left:873px">
    <div class="ico"><svg width="22" height="22" viewBox="0 0 24 24" fill="none" stroke="#fff" stroke-width="2"><circle cx="12" cy="12" r="9"/><path d="M12 7v5l3 2"/></svg></div>
    <p>Monday to Friday:<b>8:30am to 5:30pm</b></p>
  </div>
</header>

<section>
  <div class="abs hero"></div>
  <div class="abs hero-photo" role="img" aria-label="Family house with a removal truck full of boxes parked in front"></div>
  <nav class="abs navbar"><ul><li class="active">Home</li><li>Sevices</li><li>Blog</li><li>Careers</li><li>About Us</li><li>Contact Us</li></ul></nav>
  <div class="hero"><h1 class="abs"><small>Welcome to</small>Harbour Lane<br>Removals</h1><a class="abs btn">Contact Us</a></div>
</section>

<section>
  <h2 class="abs section-title" style="top:602px">Our <span class="mark">Services</span></h2>
  <div class="abs card" style="left:112px;top:712px;width:305px;height:291px">
    <div class="photo" role="img" aria-label="Worker loading stacked moving boxes" style="background:linear-gradient(135deg,#6a3a24,#3a2418 60%,#5b6a3a)"></div>
    <div class="pill" style="top:188px">Local removalists</div>
  </div>
  <div class="abs card" style="left:448px;top:712px;width:305px;height:291px">
    <div class="photo" role="img" aria-label="Removal truck outside an office building" style="background:linear-gradient(180deg,#9cc0e0,#6f8fa8 40%,#4a6178)"></div>
    <div class="pill" style="top:102px">Office Moves</div>
    <div class="overlay">Duis aute irure dolor in reprehen lor derit in volupt velit esse cillum derit in volupt velit esse dolore fugiat nulla pariatur.</div>
  </div>
  <div class="abs card" style="left:785px;top:712px;width:305px;height:291px">
    <div class="photo" role="img" aria-label="Storage unit with green door and boxes on a trolley" style="background:linear-gradient(135deg,#b9b5ae,#7fa06a 50%,#a88a62)"></div>
    <div class="pill" style="top:188px">Secure Storage</div>
  </div>
  <div class="abs card" style="left:112px;top:1029px;width:476px;height:291px">
    <div class="photo" role="img" aria-label="Two movers carrying boxes out of a van" style="background:linear-gradient(135deg,#c9a575,#5a6f8c 45%,#8aa07a)"></div>
    <div class="pill" style="top:188px">Removals cover</div>
  </div>
  <div class="abs card" style="left:614px;top:1029px;width:476px;height:291px">
    <div class="photo" role="img" aria-label="White car on a tow truck on the highway" style="background:linear-gradient(180deg,#8fb0cc,#5d6e56 50%,#8a8d8f)"></div>
    <div class="pill" style="top:188px">Vehicle Transport</div>
  </div>
</section>

<section>
  <div class="abs about-bg" role="img" aria-label="Two movers passing boxes from a van"></div>
  <div class="abs about-card">
    <h2>About <span class="mark">Us</span></h2>
    <p>Lorem ipsum dolor sit amet, consectetur adipiscing elit, sed do eiusmod tempor incididunt ut labore et dolore magna aliqua. Quis ipsum suspendisse ultrices gravida. Risus commodo viverra maecenas accumsan lacus vel facilisis.</p>
    <p>Lorem ipsum dolor sit amet, consectetur adipiscing elit, sed do eiusmod tempor incididunt ut labore et dolore magna aliqua.</p>
    <a class="btn">Learn More</a>
  </div>
</section>

<section>
  <div class="abs reviews"></div>
  <h2 class="abs section-title" style="top:2050px">What our <span class="mark">customers</span> think of us</h2>
  <div class="abs review" style="left:150px;top:2184px">
    <h3>Marcus Doyle</h3>
    <p>Ut enim ad minima veniam, quis nostr exercit lore ationem ullam corporis suscipit laborim, nisit utips aliquid ex ea commodi consequatur.</p>
    <span class="badge"></span>
  </div>
  <div class="abs quote" style="left:174px;top:2148px"><svg width="38" height="30" viewBox="0 0 38 30" fill="#fff"><circle cx="9" cy="9" r="8"/><path d="M16 10c0 9-6 16-13 18l-1-3c4-2 7-6 7-11z"/><circle cx="28" cy="9" r="8"/><path d="M35 10c0 9-6 16-13 18l-1-3c4-2 7-6 7-11z"/></svg></div>
  <div class="abs review" style="left:618px;top:2184px">
    <h3>Marcus Doyle</h3>
    <p>Ut enim ad minima veniam, quis nostr exercit lore ationem ullam corporis suscipit laborim, nisit utips aliquid ex ea commodi consequatur.</p>
    <span class="badge"></span>
  </div>
  <div class="abs quote" style="left:641px;top:2148px"><svg width="38" height="30" viewBox="0 0 38 30" fill="#fff"><circle cx="9" cy="9" r="8"/><path d="M16 10c0 9-6 16-13 18l-1-3c4-2 7-6 7-11z"/><circle cx="28" cy="9" r="8"/><path d="M35 10c0 9-6 16-13 18l-1-3c4-2 7-6 7-11z"/></svg></div>
</section>

<footer>
  <div class="abs footer"></div>
  <div class="abs news">
    <h2>Reduce the cost of <span class="mark">your fleet</span></h2>
    <p>Sign up for top tips on improving the efficiency of your plant equipment, news, updates and promotions.</p>
    <div class="signup"><span>Email Id</span><b>Submit</b></div>
  </div>

  <div class="abs footer-brand">Harbour Lane<br>Removals</div>
  <div class="abs socials"><i></i><i></i><i></i><i></i><i></i></div>
  <div class="abs copy">2024 Harbour Lane Removals.<br>All Rights Reserved</div>

  <div class="abs col" style="left:468px;top:2868px">
    <h4>CONTACT</h4>
    <div class="row"><svg width="18" height="22" viewBox="0 0 18 22" fill="#fff"><path d="M9 0a8 8 0 0 0-8 8c0 6 8 14 8 14s8-8 8-14a8 8 0 0 0-8-8zm0 11a3 3 0 1 1 0-6 3 3 0 0 1 0 6z"/></svg><span>Australia,<br>Address comes here</span></div>
    <div class="row"><svg width="18" height="18" viewBox="0 0 24 24" fill="#fff"><path d="M6.6 10.8a15 15 0 0 0 6.6 6.6l2.2-2.2a1 1 0 0 1 1-.25 11 11 0 0 0 3.6.6 1 1 0 0 1 1 1V20a1 1 0 0 1-1 1A17 17 0 0 1 3 4a1 1 0 0 1 1-1h3.5a1 1 0 0 1 1 1 11 11 0 0 0 .6 3.6 1 1 0 0 1-.25 1z"/></svg><span>+1800-555-0142</span></div>
    <div class="row"><svg width="18" height="18" viewBox="0 0 24 24" fill="#fff"><rect x="6" y="2" width="12" height="6"/><rect x="2" y="9" width="20" height="9" rx="2"/><rect x="6" y="15" width="12" height="7" fill="#17233f" stroke="#fff" stroke-width="2"/></svg><span>info@harbourlane.com</span></div>
  </div>
  <div class="abs col" style="left:783px;top:2868px">
    <h4>QUICK LINKS</h4>
    <a>About Us</a><a>Services</a><a>Blog</a><a>Careers</a>
  </div>
  <div class="abs col" style="left:975px;top:2868px">
    <h4>OTHER LINKS</h4>
    <a>Terms</a><a>Privacy Policy</a><a>Track Order</a><a>Contact</a>
  </div>
</footer>

</body>
</html>
```